Homemaking training schools needs a Business Card design

Designer, Hello!

No special requirements, good-looking enough.
--------------------------------------------------------------------------

Name: Marcus Dole
Chairman
Tel: 0574-71948263
Mobile: 13857420916
Email: kelvora@mailnest.example
Web: www.prt2019.example
Add: No.258, LanpingJie, BeiyuanQu, Ningbo, Zhejiang

LOGO
Ningbo PRT Homemaking Training School

Target Market(s)

pregnant women, mothers, infants, the elderly and families, including cleaning, cooking, nursing training.

Industry/Entity Type

Business

Contact Information for Business Card

Name: Marcus Dole
Chairman
Tel: 0574-71948263
Mobile: 13857420916
Email: kelvora@mailnest.example
Web: www.prt2019.example

LOGO

Font styles to use
Serif
Sans Serif
Decorative

Requirements
Nice to have
• Feels: clean, specifications, safety, comfort, warmth and happiness.

```html
<!DOCTYPE html>
<html lang="en">
<head>
<meta charset="UTF-8">
<title>PingRuiTang Business Card</title>
<link href="https://fonts.googleapis.com/css2?family=Montserrat:wght@500;600;700;800&family=Quicksand:wght@600;700&display=swap" rel="stylesheet">
<style>
  :root {
    --pink: #ec008c;
    --blue: #1273bf;
    --white: #ffffff;
    --ink: #1f1f1f;
    --stage: #2b2b2d;
  }
  * { margin: 0; padding: 0; box-sizing: border-box; }
  html, body { width: 1200px; height: 900px; overflow: hidden; }
  body { background: var(--stage); position: relative; font-family: "Montserrat", sans-serif; }

  .card {
    position: absolute;
    width: 600px;
    height: 343px;
    overflow: hidden;
    box-shadow: 0 14px 30px rgba(0,0,0,0.45);
  }

  /* Back side */
  .card-back { left: 80px; top: 90px; background: var(--pink); }
  .card-back .brand {
    position: absolute; left: 150px; top: 128px;
    display: flex; align-items: center; gap: 12px;
  }
  .card-back .brand-dot { width: 26px; height: 26px; border-radius: 50%; background: var(--white); }
  .card-back .brand-name {
    font-family: "Quicksand", sans-serif; font-weight: 700;
    font-size: 34px; color: var(--white);
  }
  .card-back .site {
    position: absolute; left: 336px; top: 186px;
    color: var(--white); font-weight: 600; font-size: 17px; letter-spacing: 0.3px;
  }
  .back-band { position: absolute; left: 0; bottom: 0; width: 100%; height: 28px; }
  .back-band .seg { position: absolute; bottom: 0; height: 100%; }
  .back-band .seg-a { left: 0; width: 52%; background: var(--blue); }
  .back-band .seg-b { left: 52%; width: 25%; background: var(--white); }
  .back-band .seg-c { left: 77%; width: 23%; background: var(--blue); height: 150%; }
  .card-back .back-band { overflow: visible; }

  /* Front side */
  .card-front { left: 520px; top: 470px; background: var(--white); }
  .person { position: absolute; right: 28px; top: 24px; text-align: right; }
  .person .name { color: var(--blue); font-weight: 800; font-size: 25px; letter-spacing: 0.5px; line-height: 1; }
  .person .role { color: var(--pink); font-weight: 700; font-size: 11px; letter-spacing: 0.6px; margin-top: 3px; }
  .rule { position: absolute; left: 24px; top: 58px; width: 420px; height: 1.5px; background: var(--blue); }
  .school {
    position: absolute; left: 24px; top: 66px;
    font-weight: 600; font-size: 12px; color: var(--ink);
  }
  .address {
    position: absolute; right: 28px; top: 92px; text-align: right;
    color: var(--blue); font-weight: 600; font-size: 13px; line-height: 1.45;
  }
  .contacts { position: absolute; right: 24px; top: 150px; list-style: none; }
  .contacts li {
    display: flex; justify-content: flex-end; align-items: center; gap: 6px;
    color: var(--blue); font-weight: 600; font-size: 13px; line-height: 1.45;
  }
  .contacts svg { width: 11px; height: 11px; fill: none; stroke: var(--pink); stroke-width: 2; }
  .logo {
    position: absolute; left: 40px; top: 205px;
    display: flex; align-items: center; gap: 12px;
  }
  .logo-dot { width: 22px; height: 22px; border-radius: 50%; background: var(--pink); }
  .logo-name {
    font-family: "Quicksand", sans-serif; font-weight: 700;
    font-size: 46px; color: var(--blue); line-height: 1;
  }
  .front-band { position: absolute; left: 0; bottom: 0; width: 100%; height: 26px; }
  .front-band .seg { position: absolute; bottom: 0; height: 100%; }
  .front-band .seg-a { left: 0; width: 55%; background: var(--blue); }
  .front-band .seg-b { left: 55%; width: 25%; background: var(--pink); height: 150%; }
  .front-band .seg-c { left: 80%; width: 20%; background: var(--blue); height: 200%; }
</style>
</head>
<body>

<section class="card card-back" aria-label="Business card back">
  <div class="brand">
    <span class="brand-dot"></span>
    <span class="brand-name">PingRuiTang</span>
  </div>
  <p class="site">www.prt2019.example</p>
  <div class="back-band">
    <span class="seg seg-a"></span>
    <span class="seg seg-b"></span>
    <span class="seg seg-c"></span>
  </div>
</section>

<section class="card card-front" aria-label="Business card front">
  <div class="person">
    <p class="name">MARCUS DOLE</p>
    <p class="role">CHAIRMAN</p>
  </div>
  <span class="rule"></span>
  <p class="school">Ningbo PRT Homemaking Training School</p>
  <p class="address">No.258, LanpingJie<br>BeiyuanQu, Ningbo, Zhejiang</p>
  <ul class="contacts">
    <li>0574-71948263
      <svg viewBox="0 0 12 12"><path d="M2 1.5 L4.5 1.5 L5.5 4 L4 5 Q5 7.5 7 8 L8 6.5 L10.5 7.5 L10.5 10 Q5 11 1.5 3 Z"/></svg>
    </li>
    <li>13857420916
      <svg viewBox="0 0 12 12"><rect x="3" y="1" width="6" height="10" rx="1"/></svg>
    </li>
    <li>kelvora@mailnest.example
      <svg viewBox="0 0 12 12"><rect x="1" y="2.5" width="10" height="7"/><path d="M1 2.5 L6 6.5 L11 2.5"/></svg>
    </li>
    <li>www.prt2019.example
      <svg viewBox="0 0 12 12"><circle cx="6" cy="6" r="4.8"/><path d="M1.2 6 H10.8 M6 1.2 Q3 6 6 10.8 M6 1.2 Q9 6 6 10.8"/></svg>
    </li>
  </ul>
  <div class="logo">
    <span class="logo-dot"></span>
    <span class="logo-name">PingRuiTang</span>
  </div>
  <div class="front-band">
    <span class="seg seg-a"></span>
    <span class="seg seg-b"></span>
    <span class="seg seg-c"></span>
  </div>
</section>

</body>
</html>
```